Business Card Design - VNT (company name)

Over 20 years of progressive technology design, migration and management experience that drives business objectives and streamlines operations. Continuously challenge conventions to meet and exceed business security, availability and functionality requirements. Maintain exceptional vendor relationships to ensure ongoing knowledge of emerging products and to secure preferred service agreements. Recruit and utilize top talent and foster a collegial environment that advances innovation and performance excellence. design logo using 3 arrows of different colors green, gold, blue

Industry/Entity Type

Progressive

Contact Information for Business Card

Martin K. Osgood
IT Strategist / Consultant

626.583.2907 MOsgood@vntosgood.example 4817 Brenning Court Pasadena, CA 91104

Colors
0255a3
f37122
fece3e

Requirements
Must have
• Note NEW EMAIL ADDRESS
• MOsgood@vntosgood.example
• NOTE NEW ORDER of the work I do.
• Infrastructure – Systems – Cybersecurity
Nice to have
• main color should be orange

```html
<!DOCTYPE html>
<html lang="en">
<head>
<meta charset="utf-8">
<title>VNT Business Card</title>
<link rel="stylesheet" href="https://fonts.googleapis.com/css2?family=Lato:wght@400;700&display=swap">
<style>
  :root {
    --bg: #3a3532;
    --card: #1b1c1e;
    --card-back: #161718;
    --orange: #f4a11d;
    --green: #8ed12c;
    --blue: #3f8fe6;
    --text-light: #d8d8d8;
    --text-muted: #7b7d80;
    --mark-silver: #b9bbbd;
  }
  * { margin: 0; padding: 0; box-sizing: border-box; }
  html, body {
    width: 1200px;
    height: 844px;
    overflow: hidden;
    background: var(--bg);
    font-family: "Lato", sans-serif;
  }
  .stage {
    position: relative;
    width: 1200px;
    height: 844px;
  }
  .card {
    position: absolute;
    top: 279px;
    width: 500px;
    height: 286px;
    border-radius: 4px;
    box-shadow: 0 10px 30px rgba(0,0,0,0.45);
  }
  .card--front { left: 70px; background: var(--card); }
  .card--back { left: 630px; background: var(--card-back); }

  .brand {
    position: absolute;
    left: 50px;
    top: 118px;
    display: flex;
    align-items: center;
    gap: 10px;
  }
  .brand__dot {
    width: 20px;
    height: 20px;
    border-radius: 50%;
    background: var(--orange);
  }
  .brand__name {
    font-weight: 700;
    font-size: 44px;
    letter-spacing: 2px;
    color: var(--orange);
    line-height: 1;
  }

  .contact {
    position: absolute;
    left: 250px;
    top: 66px;
    line-height: 1.25;
  }
  .contact__name {
    font-size: 21px;
    font-weight: 700;
    color: var(--orange);
  }
  .contact__role {
    font-size: 15px;
    color: var(--text-light);
    margin-bottom: 14px;
  }
  .contact__address {
    font-size: 15px;
    color: var(--green);
    margin-bottom: 14px;
  }
  .contact__line {
    font-size: 15px;
    color: var(--text-light);
    white-space: nowrap;
  }
  .contact__line span { color: var(--blue); }

  .back-mark {
    position: absolute;
    left: 0;
    right: 0;
    top: 92px;
    text-align: center;
    font-weight: 700;
    font-size: 64px;
    letter-spacing: 4px;
    color: var(--mark-silver);
    line-height: 1;
  }
  .services {
    position: absolute;
    left: 0;
    right: 0;
    bottom: 56px;
    text-align: center;
    font-size: 10px;
    letter-spacing: 1.1px;
    text-transform: uppercase;
    color: var(--text-muted);
    white-space: nowrap;
  }
</style>
</head>
<body>
  <main class="stage">
    <section class="card card--front">
      <div class="brand">
        <span class="brand__dot"></span>
        <span class="brand__name">VNT</span>
      </div>
      <div class="contact">
        <p class="contact__name">Martin K. Osgood</p>
        <p class="contact__role">IT Strategist / Consultant</p>
        <p class="contact__address">4817 Brenning Court<br>Pasadena, CA 91104</p>
        <p class="contact__line">M: <span>626.583.2907</span></p>
        <p class="contact__line">E: <span>MOsgood@vntosgood.example</span></p>
      </div>
    </section>

    <section class="card card--back">
      <p class="back-mark">VNT</p>
      <p class="services">IT Strategist &nbsp;|&nbsp; Consultant &nbsp;|&nbsp; Infrastructure &nbsp;|&nbsp; Systems &nbsp;|&nbsp; Cybersecurity</p>
    </section>
  </main>
</body>
</html>
```